PixelHerd CEO needs a Crowdsourced Graphic for a ByteLoom Article

I need a simple graphic / banner for a blog post that's going to be posted on ByteLoom (www.byteloom-example.net) - the biggest tech blog in the world.

The article will be written by Roan Petrie (PixelHerd's CEO) and the title will be "Asia's Secret Crowdsourcing Boom". The article is about the tens of thousands of people using crowdsourcing websites (like PixelHerd.example, TaskVane.example and Gigmoor.example) in China, India, the Philippines, Australia and other countries in the Asia Pacific region.

We'd really like to get this ASAP - so early submissions encouraged. We will try and get the winning designer linked to from the article.

Thanks to everyone that submitted!  Some great designs and hard to choose! :)

Target Market(s)

Tech saavy readers, English speakers

Industry/Entity Type

Tech

Requirements
Must have
• The graphic SHOULD:
1) Have the text "Asia's secret crowdsourcing boom" with some nice design and fonts (consider grey subtle pattern background and white drop shadow on fonts) - see attached examples
2) Have an Asian theme
3) Have the dimensions 640px wide by 240px wide
Nice to have
• The graphic COULD:
1) Have references to some or all of the countries mentioned above or use Asian characters as part of the background / motif (maybe the word "crowd" or "crowd sourcing" in different languages). In Chinese, the word for crowdsourcing is "witkey" (and there are corresponding Chinese characters: ??)
2) Emphasize the word "Asia" (using color and larger/different font)
3) Use a chart showing exponential (i.e. fast) growth - like the attached
4) Have a second line of text "5 Things You Didn't Know About Crowdsourcing in Asia"

```html
<!DOCTYPE html>
<html lang="en">
<head>
<meta charset="utf-8">
<title>Asia's Secret Crowdsourcing Boom</title>
<link rel="stylesheet" href="https://fonts.googleapis.com/css2?family=Cabin:wght@500;600&family=Questrial&family=Noto+Sans+Devanagari:wght@600&family=Noto+Sans+SC:wght@500&display=swap">
<style>
  :root {
    --bg: #ebebeb;
    --bg-stripe: #e4e4e4;
    --motif: #c9c9c9;
    --red: #c4161c;
    --red-dark: #a30f14;
    --ink: #3a3a3a;
    --chart-fill: #d6d8df;
    --hands: #9a9a9a;
    --white: #ffffff;
  }
  html, body {
    margin: 0;
    padding: 0;
    overflow: hidden;
  }
  .banner {
    position: relative;
    width: 1200px;
    height: 450px;
    overflow: hidden;
    background: repeating-linear-gradient(135deg, var(--bg) 0 6px, var(--bg-stripe) 6px 8px);
  }
  .motif-word {
    position: absolute;
    margin: 0;
    color: var(--motif);
    font-family: "Noto Sans SC", "Noto Sans Devanagari", sans-serif;
    line-height: 1;
    white-space: nowrap;
  }
  .motif-word.hindi { font-family: "Noto Sans Devanagari", sans-serif; }
  .motif-word.latin { font-family: "Cabin", sans-serif; font-weight: 600; }
  .hands {
    position: absolute;
    left: 610px;
    top: 50px;
    width: 520px;
    height: 380px;
    border-radius: 45% 45% 10% 10%;
    background: radial-gradient(ellipse at 50% 55%, rgba(120,120,120,0.45), rgba(150,150,150,0.15) 60%, rgba(150,150,150,0) 75%);
  }
  .chart {
    position: absolute;
    left: 0;
    top: 0;
  }
  .mandala {
    position: absolute;
    left: 15px;
    top: 56px;
    width: 188px;
    height: 188px;
    border-radius: 50%;
    background: radial-gradient(circle, #6b6b6b 0%, #9c9c9c 35%, #5a5a5a 60%, #8a8a8a 80%, rgba(200,200,200,0) 100%);
  }
  .headline {
    position: absolute;
    left: 222px;
    top: 14px;
    margin: 0;
    color: var(--red);
    font-family: "Cabin", sans-serif;
    font-weight: 500;
    text-shadow: 2px 2px 0 var(--white);
  }
  .headline-asia {
    display: block;
    font-size: 142px;
    line-height: 1;
    letter-spacing: -1px;
  }
  .headline-rest {
    display: block;
    margin-top: -4px;
    font-size: 60px;
    line-height: 1;
    letter-spacing: 0.5px;
  }
  .subtitle {
    position: absolute;
    left: 225px;
    top: 244px;
    display: flex;
    align-items: center;
    margin: 0;
  }
  .subtitle-number {
    display: flex;
    align-items: center;
    justify-content: center;
    width: 40px;
    height: 50px;
    background: var(--white);
    border: 2px solid #8a8a8a;
    border-radius: 6px;
    color: var(--ink);
    font-family: "Questrial", sans-serif;
    font-size: 40px;
    box-shadow: 1px 2px 3px rgba(0,0,0,0.25);
  }
  .subtitle-text {
    padding: 3px 16px 3px 12px;
    background: var(--white);
    color: var(--ink);
    font-family: "Questrial", sans-serif;
    font-size: 25px;
    font-style: italic;
    letter-spacing: 0.5px;
    border-radius: 0 4px 4px 0;
    box-shadow: 1px 2px 3px rgba(0,0,0,0.2);
  }
</style>
</head>
<body>
<div class="banner">
  <p class="motif-word hindi" style="left:60px;top:18px;font-size:40px;">भीड</p>
  <p class="motif-word" style="left:175px;top:4px;font-size:40px;">众包</p>
  <p class="motif-word latin" style="left:372px;top:6px;font-size:38px;">karamihan ng tao</p>
  <p class="motif-word" style="left:740px;top:2px;font-size:40px;">众包</p>
  <p class="motif-word hindi" style="left:745px;top:106px;font-size:34px;">भीड</p>
  <p class="motif-word" style="left:565px;top:80px;font-size:36px;">众包</p>
  <p class="motif-word hindi" style="left:610px;top:136px;font-size:34px;">भीड</p>
  <p class="motif-word" style="left:855px;top:100px;font-size:40px;">众包</p>
  <p class="motif-word" style="left:1000px;top:2px;font-size:44px;">众包</p>
  <p class="motif-word hindi" style="left:1110px;top:60px;font-size:36px;">भीड</p>
  <p class="motif-word" style="left:60px;top:260px;font-size:34px;">众包</p>
  <p class="motif-word hindi" style="left:30px;top:360px;font-size:34px;">भीड</p>

  <div class="hands" role="img" aria-label="Silhouettes of many raised hands in grey"></div>

  <svg class="chart" width="1200" height="450" viewBox="0 0 1200 450" aria-hidden="true">
    <path d="M420 450 L491 412 L666 375 L919 349 L1149 278 L1200 169 L1200 450 Z" fill="var(--chart-fill)"/>
    <polyline points="420,450 491,412 666,375 919,349 1149,278 1200,169" fill="none" stroke="var(--red)" stroke-width="5" stroke-linejoin="round"/>
    <g fill="var(--red)" stroke="var(--white)" stroke-width="3">
      <circle cx="491" cy="412" r="15"/>
      <circle cx="666" cy="375" r="15"/>
      <circle cx="919" cy="349" r="15"/>
      <circle cx="1149" cy="278" r="15"/>
    </g>
  </svg>

  <div class="mandala" role="img" aria-label="Circular mandala ornament in black and white"></div>

  <h1 class="headline">
    <span class="headline-asia">Asia's</span>
    <span class="headline-rest">secret crowdsourcing boom</span>
  </h1>

  <p class="subtitle">
    <span class="subtitle-number">5</span>
    <span class="subtitle-text">Things You Didn't Know About Crowdsourcing in Asia</span>
  </p>
</div>
</body>
</html>
```